Halvery Construction Group Website

Need a dynamic corporate website that can be built on with time. We want to get our information out to the world and have a place where customers can submit requests for proposals.

Target Market(s)

Custom home owners and buyers. Architects and Real Estate Agents.

Industry/Entity Type

Construction

Number of Pages Required

3 page

Font styles to use
Serif
Sans Serif

Requirements
Must have
• Company logo, about, company contact information, biography, contact, projects,
• Sleek, modern, clean, attractive design.
• Online form customers can use for filling out a request for project proposal.
• Linkedin hyperlink.
• Uses www.halveryconstructiongroup.example

```html
<!DOCTYPE html>
<html lang="en">
<head>
<meta charset="utf-8">
<title>Halvery Construction Group</title>
<link rel="stylesheet" href="https://fonts.googleapis.com/css2?family=Open+Sans:wght@300;400;600;700&display=swap">
<style>
:root{
  --night:#0d1118;
  --navy-deep:#131b26;
  --navy:#1e2836;
  --accent:#4a97dd;
  --white:#ffffff;
  --ink:#1e2836;
  --muted:#666b72;
  --footer-bg:#eeeeee;
  --footer-line:#dcdcdc;
  --brand-blue:#1f5fae;
}
*{margin:0;padding:0;box-sizing:border-box}
html,body{width:881px;height:1200px;overflow:hidden}
body{font-family:"Open Sans",Arial,sans-serif;background:var(--white);position:relative;color:var(--ink)}
.page{position:relative;width:881px;height:1200px;overflow:hidden}

.hero{position:absolute;left:0;top:0;width:881px;height:470px;background:var(--night)}
.hero-photo{position:absolute;inset:0;background:
  radial-gradient(ellipse 60% 35% at 60% 75%,rgba(214,120,30,.55),transparent 70%),
  radial-gradient(ellipse 30% 50% at 40% 35%,rgba(180,80,30,.35),transparent 70%),
  linear-gradient(180deg,#0b0e13 0%,#1b1d22 35%,#3a2b1c 60%,#17130f 100%)}
.hero-shade{position:absolute;inset:0;background:rgba(0,0,0,.3)}
.brand{position:absolute;left:73px;top:33px;display:flex;align-items:center;gap:9px;color:var(--white)}
.brand-mark{width:46px;height:46px;background:var(--white)}
.brand-name{font-size:27px;font-weight:600;letter-spacing:1px;line-height:1}
.brand-sub{display:block;font-size:8.5px;font-weight:400;letter-spacing:.3px;margin-top:3px}
.nav{position:absolute;top:49px;left:0;width:881px;list-style:none}
.nav li{position:absolute;font-size:9.5px;font-weight:700;color:var(--white);text-transform:uppercase}
.hero-title{position:absolute;left:0;top:193px;width:881px;text-align:center;color:var(--white);font-weight:300;font-size:29px;line-height:37px;text-transform:uppercase}
.hero-sub{position:absolute;left:0;top:278px;width:881px;text-align:center;color:var(--white);font-weight:300;font-size:13px;text-transform:uppercase}
.btn{position:absolute;background:var(--accent);color:var(--white);font-size:10px;font-weight:600;text-transform:uppercase;display:flex;align-items:center;justify-content:center;border-radius:2px;letter-spacing:.2px}
.dots{position:absolute;left:840px;top:189px;width:7px}
.dots span{display:block;width:6px;height:6px;border-radius:50%;background:#8a8a8a;margin-bottom:12px}
.dots span:first-child{background:transparent;border:1px solid #9a9a9a}

.service{position:absolute;top:470px;height:280px;width:441px;text-align:center;color:var(--white)}
.service.left{left:0;background:var(--navy-deep)}
.service.right{left:440px;width:441px;background:var(--navy)}
.service svg{position:absolute;left:50%;transform:translateX(-50%)}
.service h2{position:absolute;left:0;width:100%;font-weight:400;font-size:19px;text-transform:uppercase}
.service p{position:absolute;left:70px;width:300px;font-size:7.6px;line-height:17.6px}

.about{position:absolute;top:750px;left:0;width:881px;height:226px;text-align:center}
.about h2{position:absolute;top:51px;width:100%;font-weight:400;font-size:19.5px;text-transform:uppercase;color:var(--ink)}
.about p{position:absolute;top:89px;left:160px;width:561px;font-size:9.8px;line-height:19.6px;color:var(--muted)}

.footer{position:absolute;top:976px;left:0;width:881px;height:176px;background:var(--footer-bg);border-top:1px solid var(--footer-line);border-bottom:1px solid var(--footer-line)}
.footer-brand{position:absolute;left:74px;top:73px;display:flex;align-items:center;gap:6px;color:var(--brand-blue)}
.footer-brand .brand-mark{width:30px;height:30px;background:var(--brand-blue)}
.footer-brand .brand-name{font-size:20px}
.footer-brand .brand-sub{font-size:6px}
.col{position:absolute;top:35px}
.col h3{font-size:10.8px;font-weight:600;text-transform:uppercase;color:var(--ink);line-height:14px;letter-spacing:.2px}
.col ul{list-style:none;margin-top:6px}
.col li{font-size:8px;line-height:17.6px;color:var(--muted);display:flex;align-items:center;gap:5px}
.social{display:flex;gap:6px;margin-top:11px}
.social span{width:21px;height:21px;border-radius:50%;background:var(--brand-blue)}
.copyright{position:absolute;top:1170px;left:0;width:881px;text-align:center;font-size:7.8px;color:var(--muted)}
</style>
</head>
<body>
<div class="page">
  <header class="hero">
    <div class="hero-photo" role="img" aria-label="Night photograph of a large suspension bridge lit in orange over the bay with city lights behind"></div>
    <div class="hero-shade"></div>
    <div class="brand">
      <span class="brand-mark"></span>
      <span class="brand-name">HALVERY<span class="brand-sub">CONSTRUCTION GROUP, INC.</span></span>
    </div>
    <ul class="nav">
      <li style="left:463px">Home</li>
      <li style="left:540px">About</li>
      <li style="left:621px">Bio</li>
      <li style="left:687px">Projects</li>
      <li style="left:779px">Contact Us</li>
    </ul>
    <h1 class="hero-title">Commercial, Residential and<br>Community Solutions</h1>
    <p class="hero-sub">We offer full-scale renovations and new custom construction.</p>
    <a class="btn" style="left:382px;top:316px;width:117px;height:34px">Read More Info</a>
    <div class="dots"><span></span><span></span><span></span><span></span><span></span></div>
  </header>

  <section class="service left">
    <svg style="top:33px" width="40" height="40" viewBox="0 0 40 40" fill="none" stroke="#fff" stroke-width="2">
      <path d="M8 24 A12 12 0 0 1 32 24"/>
      <path d="M4 24 H36 V28 H4 Z"/>
      <path d="M20 12 V20 M16 13 V21 M24 13 V21"/>
    </svg>
    <h2 style="top:107px">Construction Solutions</h2>
    <p style="top:142px">Lorem Ipsum es simplemente el texto de relleno de las imprentas y archivos de texto. Lorem Ipsum ha sido el texto de relleno estándar de las industrias desde el año 1500, cuando un impresor...</p>
    <a class="btn" style="left:162px;top:211px;width:117px;height:34px">Read More Info</a>
  </section>

  <section class="service right">
    <svg style="top:38px" width="50" height="52" viewBox="0 0 50 52" fill="none" stroke="#fff" stroke-width="2">
      <rect x="1" y="1" width="30" height="50"/>
      <rect x="31" y="13" width="18" height="38"/>
      <g fill="#fff" stroke="none">
        <rect x="6" y="7" width="4" height="4"/><rect x="14" y="7" width="4" height="4"/><rect x="22" y="7" width="4" height="4"/>
        <rect x="6" y="15" width="4" height="4"/><rect x="14" y="15" width="4" height="4"/><rect x="22" y="15" width="4" height="4"/>
        <rect x="6" y="23" width="4" height="4"/><rect x="14" y="23" width="4" height="4"/><rect x="22" y="23" width="4" height="4"/>
        <rect x="6" y="31" width="4" height="4"/><rect x="14" y="31" width="4" height="4"/><rect x="22" y="31" width="4" height="4"/>
        <rect x="6" y="39" width="4" height="4"/><rect x="14" y="39" width="4" height="4"/><rect x="22" y="39" width="4" height="4"/>
        <rect x="36" y="19" width="8" height="3"/><rect x="36" y="26" width="8" height="3"/><rect x="36" y="33" width="8" height="3"/><rect x="36" y="40" width="8" height="3"/>
      </g>
    </svg>
    <h2 style="top:104px">Enterprise Services</h2>
    <p style="top:140px">Lorem Ipsum es simplemente el texto de relleno de las imprentas y archivos de texto. Lorem Ipsum ha sido el texto de relleno estándar de las industrias desde el año 1500, cuando un impresor...</p>
    <a class="btn" style="left:162px;top:209px;width:117px;height:34px">Read More Info</a>
  </section>

  <section class="about">
    <h2>About Halvery Construction Group</h2>
    <p>Lorem Ipsum es simplemente el texto de relleno de las imprentas y archivos de texto. Lorem Ipsum ha sido el texto de relleno estándar de las industrias desde el año 1500, cuando un impresor (N. del T. persona que se dedica a la imprenta) desconocido usó una galería de textos y los mezcló de tal manera que logró hacer un libro de textos especimen.</p>
    <a class="btn" style="left:379px;top:164px;width:123px;height:33px">Read More Info</a>
  </section>

  <footer class="footer">
    <div class="footer-brand">
      <span class="brand-mark"></span>
      <span class="brand-name">HALVERY<span class="brand-sub">CONSTRUCTION GROUP, INC.</span></span>
    </div>
    <div class="col" style="left:264px">
      <h3>Welcome</h3>
      <ul><li>Home</li><li>About</li><li>Bio</li><li>Projects</li><li>Contact us</li></ul>
    </div>
    <div class="col" style="left:371px">
      <h3>Information</h3>
      <ul><li>Terms &amp; Conditions</li><li>Privacy Policy</li><li>Disclaimer</li><li>Sitemap</li></ul>
    </div>
    <div class="col" style="left:496px">
      <h3>Contact Info</h3>
      <ul>
        <li>48 Larkmoor Avenue</li>
        <li>2nd Floor, Dunmere, Ohio 45990</li>
        <li><svg width="8" height="8" viewBox="0 0 8 8"><path d="M1 1 L3 1 L3.6 2.6 L2.6 3.3 Q3.5 4.8 4.7 5.4 L5.4 4.4 L7 5 L7 7 Q3 7.2 1 1 Z" fill="#4a97dd"/></svg>Phone : ( 0000 ) 555 014</li>
        <li><svg width="9" height="7" viewBox="0 0 9 7" fill="none" stroke="#4a97dd"><rect x=".5" y=".5" width="8" height="6"/><path d="M.5 .5 L4.5 4 L8.5 .5"/></svg>E-mail: info@halveryconstruction.example</li>
      </ul>
    </div>
    <div class="col" style="left:679px">
      <h3>Connect with our<br>social network</h3>
      <div class="social" aria-label="Social network links"><span></span><span></span><span></span><span></span><span></span></div>
    </div>
  </footer>
  <p class="copyright">© 2016. Halvery Construction. All rights reserved.</p>
</div>
</body>
</html>
```